Visitenkarten/Briefpaier/Kassenkassenbelege für Juwelier
Zielgruppe
Mittelständischer Juwelier mit zwei Filialen. Klassischer Schmuck, Uhren und Modeschmuck
Aufgabenstellung
Es müssen für zwei Geschäfte Visitenkarten, Briefpapier (A4) und Kassenkassenbelege (A6) erstellt werden. Logo und Typo im Anhang. Ein Farbkonzept besteht noch nicht. Die Idee geht in Richtung Bordeaux-Rot.
Generell:
(1) Sieht erstmal nach viel Beschreibung aus, bitte nicht entmutigen lassen, sind zu 90% nur austauschbare Inhalts-/Kontaktdaten.
(2) Für meine Zwecke reicht es vollkommen aus, wenn bei den Vorschlägen zur Arbeitsersparnis erstmal nur mit einer Adresse gearbeitet wird. Wenn ich dann den zutreffenden Designvorschlag gefunden habe, können wir die zweite Adresse in dem ersten Format umsetzen. Ich denke das spart Zeit und Nerven.
(3) Bitte Angaben wie "Tel.:" oder "USt.- ID:" nicht wörtlich nehmen, es soll dabei klar sein worum es geht; wenn "Telefon" ausgeschrieben besser aussieht, bitte in der optisch ansprechenderen Form verwenden.
(4) Bei Fragen, bitte fragen!
(5) Viel Spass bei dem Projekt - Ich freu' mich auf die Vorschläge!
Visitenkarten(1):
Juwelier Brenneck GmbH
www.juwelier-brenneck-beispiel.de
Visitenkarten(2):
Visitenkarten(generell):
(1) Die einzelnen Daten können durch Hervorhebungen wie Adresse, Kontakt, Online/Internet unterteilt bzw. hervorgehoben werden.
(2) Die Visitenkarten sollen farbig gedruckt werden; geplant ist weiß als Hintergrund ist aber nicht zwingend bei einer guten anderen Idee
Briefpapier:
(1)Absender im Adressfeld für DIN-lang Briefumschläge mit Fenster:
(2)Informationen im Footer/Seitenbereich:
Juwelier Brenneck Gmb..

```html
<!DOCTYPE html>
<html lang="de">
<head>
<meta charset="utf-8">
<title>Juwelier Brenneck – Geschäftsausstattung</title>
<link rel="stylesheet" href="https://fonts.googleapis.com/css2?family=Source+Sans+3:wght@400;600&display=swap">
<style>
  :root {
    --backdrop: #55514c;
    --paper: #f2f2f2;
    --ink: #111111;
    --label: #b0b0b0;
    --brand-grey: #a8a8a8;
    --card-dark: #000000;
    --card-light-text: #d9d9d9;
    --frame: #333333;
  }
  * { margin: 0; padding: 0; box-sizing: border-box; }
  html, body { width: 1200px; height: 978px; overflow: hidden; }
  body {
    background: var(--backdrop);
    font-family: "Source Sans 3", "Helvetica Neue", Arial, sans-serif;
    position: relative;
  }
  .letterhead {
    position: absolute;
    left: 292px; top: 42px;
    width: 645px; height: 913px;
    background: var(--paper);
  }
  .tab {
    position: absolute;
    width: 33px;
    background: var(--card-dark);
    left: 50%; transform: translateX(-50%);
  }
  .letterhead > .tab-top { top: 0; height: 59px; }
  .letterhead > .tab-bottom { bottom: 0; height: 15px; }
  .brand-name {
    position: absolute;
    left: 0; right: 0;
    text-align: center;
    font-weight: 600;
    font-size: 18px;
    letter-spacing: 0.5px;
    text-transform: uppercase;
    color: var(--brand-grey);
  }
  .letterhead > .brand-name { top: 76px; }
  .sender-line {
    position: absolute;
    top: 151px; right: 42px;
    font-size: 7.5px;
    color: var(--ink);
    white-space: nowrap;
  }
  .label { color: var(--label); }
  .sep { display: inline-block; width: 8px; }
  .card {
    position: absolute;
    width: 277px; height: 169px;
    overflow: hidden;
  }
  .card-dark { left: 190px; top: 344px; background: var(--card-dark); }
  .card-light { left: 192px; top: 531px; background: var(--paper); border: 1px solid var(--frame); }
  .card .tab { top: 0; height: 62px; }
  .card-dark .tab { background: var(--paper); }
  .card .brand-name { top: 76px; font-size: 17px; }
  .card-dark .brand-name { color: var(--card-light-text); }
  .footer {
    position: absolute;
    left: 0; right: 0; top: 832px;
    text-align: center;
    font-size: 7.5px;
    line-height: 12px;
    color: var(--ink);
  }
</style>
</head>
<body>
  <main class="letterhead">
    <div class="tab tab-top"></div>
    <div class="brand-name">Juwelier Brenneck</div>

    <p class="sender-line">
      <span class="label">JUWELIER BRENNECK GmbH</span><span class="sep"></span>Lindenallee 12 in 45127 Musterstadt<span class="sep"></span><span class="sep"></span>
      <span class="label">TEL</span> 0123-456780 <span class="label">FAX</span> 0123-456781<span class="sep"></span>
      <span class="label">info@</span>juwelier-brenneck-beispiel.de<span class="sep"></span>
      <span class="label">www.</span>juwelier-brenneck-beispiel.de
    </p>

    <section class="card card-dark" aria-label="Visitenkarte Vorderseite">
      <div class="tab"></div>
      <div class="brand-name">Juwelier Brenneck</div>
    </section>

    <section class="card card-light" aria-label="Visitenkarte Rückseite">
      <div class="tab"></div>
      <div class="brand-name">Juwelier Brenneck</div>
    </section>

    <footer class="footer">
      <p><span class="label">Juwelier Brenneck GmbH</span>&nbsp; Lindenallee 12 in 45127 Musterstadt</p>
      <p><span class="label">Geschäftsführer</span> Marlene Brenneck&nbsp; <span class="label">Amtsgericht Musterstadt</span> HRB 10000&nbsp; <span class="label">Steuernummer</span> 100/2000/3000&nbsp; <span class="label">USt.- ID</span> DE 100200300</p>
      <p><span class="label">Bank</span> Musterbank AG Musterstadt&nbsp; <span class="label">IBAN</span> DE00 1234 5678 9012 3456 78&nbsp; <span class="label">BIC</span> MUST DE 1X</p>
    </footer>

    <div class="tab tab-bottom"></div>
  </main>
</body>
</html>
```